Satchel & Sundial needs new business card design

I need a new business card design. I'm looking for out-of-the-box design which represents the freedom of being a location independent entrepreneur.
I offer coaching, retreats and trips.
I would like to see designs with and without the photo.
Colors I use are black (#000000), green (#25A796) and brown (#D7C38C)
Website satchelandsundial.example

Target Market(s)

location independent entrepreneurs, digital nomads, people looking to swap the 9 to 5 for a lifestyle business

Industry/Entity Type

Business

Contact Information for Business Card

Dorota Falkner
Your Lifestyle Business Coach, Retreat & Trip Leader
http://satchelandsundial.example
hello@satchelandsundial.example
Live a life you don't need a holiday from

Font styles to use
Serif
Sans Serif

Requirements
Must have
• One side should contain only the logo. I would also consider having the "Live a life you don't need a holiday from" on that side too (depending on how it looks)
• Please show both sides on the designs.

```html
<!DOCTYPE html>
<html lang="en">
<head>
<meta charset="utf-8">
<title>Satchel &amp; Sundial — Business Card</title>
<link rel="stylesheet" href="https://fonts.googleapis.com/css2?family=Amatic+SC:wght@700&family=Open+Sans:wght@400;700&display=swap">
<style>
  :root {
    --stage-top: #2e2e2e;
    --stage-bottom: #000000;
    --card: #d7c38c;
    --ink: #000000;
    --accent: #25a796;
  }
  * { margin: 0; padding: 0; box-sizing: border-box; }
  html, body { width: 1200px; height: 900px; overflow: hidden; }
  body {
    position: relative;
    background: linear-gradient(180deg, var(--stage-top) 0%, #151515 55%, var(--stage-bottom) 100%);
    font-family: "Open Sans", Arial, sans-serif;
    color: var(--ink);
  }
  .card-shapes { position: absolute; left: 0; top: 0; }
  .card-shape { fill: var(--card); }

  .front-details { position: absolute; left: 180px; top: 341px; }
  .holder-name { font-size: 15px; font-weight: 700; line-height: 20px; }
  .holder-role { font-size: 12px; line-height: 16px; margin-top: 1px; }
  .contact-list { list-style: none; margin-top: 10px; font-size: 12px; line-height: 17px; }
  .contact-list li { display: flex; align-items: center; gap: 4px; }
  .contact-icon { width: 8px; height: 8px; fill: var(--ink); }

  .wordmark {
    position: absolute;
    font-family: "Amatic SC", "Comic Sans MS", cursive;
    font-weight: 700;
    color: var(--ink);
    line-height: 1;
    white-space: nowrap;
  }
  .wordmark--front { left: 356px; top: 448px; font-size: 42px; }
  .wordmark--back { left: 757px; top: 392px; font-size: 52px; }

  .tagline {
    position: absolute;
    left: 180px; top: 527px;
    font-family: "Amatic SC", "Comic Sans MS", cursive;
    font-weight: 700;
    font-size: 17px;
    letter-spacing: 1.6px;
    text-transform: uppercase;
  }
</style>
</head>
<body>
  <svg class="card-shapes" width="1200" height="900" viewBox="0 0 1200 900" aria-hidden="true">
    <path class="card-shape card-shape--front"
      d="M161,306 H562 C548,306 540,316 540,332 C540,372 560,402 584,452 C600,484 606,512 606,545 C606,565 592,577 572,577 H161 Q149,577 149,565 V318 Q149,306 161,306 Z"/>
    <path class="card-shape card-shape--back"
      d="M1036,306 H636 C650,306 657,316 657,332 C657,372 638,402 622,452 C612,484 608,512 608,545 C608,565 620,577 642,577 H1036 Q1048,577 1048,565 V318 Q1048,306 1036,306 Z"/>
  </svg>

  <section class="card card--front">
    <div class="front-details">
      <h1 class="holder-name">Dorota Falkner</h1>
      <p class="holder-role">Your Lifestyle Business Coach,<br>Retreat &amp; Trip Leader</p>
      <ul class="contact-list">
        <li>
          <svg class="contact-icon" viewBox="0 0 8 8" aria-hidden="true"><rect x="0" y="1" width="8" height="6"/><path d="M0 1 L4 4.5 L8 1" fill="none" stroke="#d7c38c" stroke-width="0.9"/></svg>
          hello@satchelandsundial.example
        </li>
        <li>
          <svg class="contact-icon" viewBox="0 0 8 8" aria-hidden="true"><circle cx="4" cy="4" r="4"/></svg>
          www.satchelandsundial.example
        </li>
      </ul>
    </div>
    <div class="wordmark wordmark--front">Satchel &amp; Sundial</div>
    <p class="tagline">Live a life you don't need a holiday from</p>
  </section>

  <section class="card card--back">
    <div class="wordmark wordmark--back">Satchel &amp; Sundial</div>
  </section>
</body>
</html>
```